Heating and Cooling Company mobile website

We need a website specifically designed for a viewing on a mobile device.

We serve the northern New Jersey heating, cooling and electrical residential market.

The goal is the drive traffic to the site by using Brintel Pay Per click. People will be searching for an HVAC contractor, and they land on our page. They need to get key info quickly without all the clutter of a desktop type of site.

Target Market(s)

Homeowners

Industry/Entity Type

Hvac

Coding

Coded - Design and coding required

Number of Pages Required

5+ page

Font styles to use
Serif

Requirements
Must have
• View attachments to see samples of the desktop version. It must have a similar color scheme
• The copy of the website is also attached
Nice to have
• Would like it to have a sort of Vardok feel to it. Make it seem like its an app that people are using and that its exciting to be on the website. It would be nice to have a page where customers can book appointments

```html
<!DOCTYPE html>
<html lang="en">
<head>
<meta charset="utf-8">
<title>HVAC Mobile Site – Navigation</title>
<link rel="stylesheet" href="https://fonts.googleapis.com/css2?family=Montserrat:wght@500&family=Roboto+Slab:wght@400&display=swap">
<style>
  :root {
    --drawer-bg: #2f3652;
    --drawer-divider: #252b43;
    --drawer-text: #ffffff;
    --page-dim: #3b3b3d;
    --header-dim: #28282a;
    --footer-dim: #141416;
    --accent-dim: #6e4516;
    --accent-icon: #4a2e0e;
    --heading-dim: #1f1f21;
    --photo-dim-a: #2c2c2e;
    --photo-dim-b: #4a3a30;
    --close-icon: #ffffff;
  }
  * { box-sizing: border-box; margin: 0; padding: 0; }
  html, body {
    width: 752px;
    height: 1200px;
    overflow: hidden;
    background: var(--page-dim);
  }
  .screen {
    position: relative;
    width: 752px;
    height: 1200px;
    overflow: hidden;
    background: var(--page-dim);
  }
  .page-header {
    position: absolute;
    left: 0; top: 0;
    width: 752px; height: 194px;
    background: var(--header-dim);
  }
  .close-button {
    position: absolute;
    left: 608px; top: 36px;
    width: 66px; height: 66px;
  }
  .call-badge {
    position: absolute;
    left: 595px; top: 228px;
    width: 114px; height: 114px;
    border-radius: 50%;
    background: var(--accent-dim);
    display: flex; align-items: center; justify-content: center;
  }
  .page-title {
    position: absolute;
    left: 690px; top: 420px;
    font-family: "Roboto Slab", serif;
    font-size: 40px;
    color: var(--heading-dim);
    white-space: nowrap;
  }
  .hero-photo {
    position: absolute;
    left: 569px; top: 790px;
    width: 183px; height: 300px;
    background: linear-gradient(135deg, var(--photo-dim-a), var(--photo-dim-b));
    border-radius: 40px 0 0 30px;
  }
  .page-footer {
    position: absolute;
    left: 0; top: 1127px;
    width: 752px; height: 73px;
    background: var(--footer-dim);
  }
  .nav-drawer {
    position: absolute;
    left: 0; top: 0;
    width: 546px; height: 1200px;
    background: var(--drawer-bg);
  }
  .nav-list { list-style: none; }
  .nav-item {
    height: 155px;
    display: flex;
    align-items: center;
    padding-left: 78px;
    border-bottom: 2px solid var(--drawer-divider);
    font-family: "Montserrat", sans-serif;
    font-weight: 500;
    font-size: 32px;
    letter-spacing: 0.5px;
    color: var(--drawer-text);
  }
</style>
</head>
<body>
<div class="screen">
  <header class="page-header"></header>
  <svg class="close-button" viewBox="0 0 66 66" aria-label="Close menu">
    <path d="M4 4 L62 62 M62 4 L4 62" stroke="var(--close-icon)" stroke-width="4" stroke-linecap="round"/>
  </svg>
  <div class="call-badge">
    <svg width="52" height="52" viewBox="0 0 24 24" aria-label="Call">
      <path fill="var(--accent-icon)" d="M6.6 10.8a15.1 15.1 0 0 0 6.6 6.6l2.2-2.2c.3-.3.7-.4 1-.2 1.1.4 2.3.6 3.6.6.6 0 1 .4 1 1V20c0 .6-.4 1-1 1A17 17 0 0 1 3 4c0-.6.4-1 1-1h3.5c.6 0 1 .4 1 1 0 1.3.2 2.5.6 3.6.1.3 0 .7-.2 1z"/>
    </svg>
  </div>
  <h1 class="page-title">Mo</h1>
  <div class="hero-photo" role="img" aria-label="Photo of a branded company service truck"></div>
  <footer class="page-footer"></footer>

  <nav class="nav-drawer">
    <ul class="nav-list">
      <li class="nav-item">HOME</li>
      <li class="nav-item">ABOUT</li>
      <li class="nav-item">HVAC COOLING</li>
      <li class="nav-item">HVAC HEATING</li>
      <li class="nav-item">PRODUCTS</li>
      <li class="nav-item">SERVICES</li>
      <li class="nav-item">CONTACT US</li>
      <li class="nav-item">BLOG</li>
    </ul>
  </nav>
</div>
</body>
</html>
```